Need to drive pregnant women to my 3d4d ultrasound studio where i provide 4d ultrasound with hyperalistic imaging and gender reveals

Industry/Entity Type

Healthcare

Font styles to use
Decorative
Script

Requirements
Must have
• My Company name Cielo de Nuestra Espera 4D. EVERYTHING HAS TO BE IN SPANISH
Nice to have
• SIMPLE AND NOT TOO BUSY
Should not have
• website

```html
<!DOCTYPE html>
<html lang="es">
<head>
<meta charset="UTF-8">
<title>Cielo de Nuestra Espera 4D — Valla</title>
<link rel="stylesheet" href="https://fonts.googleapis.com/css2?family=Archivo+Black&family=Poppins:wght@400;500;600&display=swap">
<style>
  :root {
    --cream: #f7dcc0;
    --maroon: #6b1420;
    --navy: #0d2377;
    --ink: #151515;
    --white: #ffffff;
    --phone-red: #c1272d;
    --number: #f7dcc0;
    --page: #eef1f4;
  }
  * { margin: 0; padding: 0; box-sizing: border-box; }
  html, body {
    width: 1200px; height: 900px; overflow: hidden;
    background: var(--page);
  }
  .billboard {
    position: absolute; left: 20px; top: 230px;
    width: 1160px; height: 440px;
    background: var(--cream);
    overflow: hidden;
    box-shadow: 0 6px 20px rgba(0,0,0,0.15);
  }
  .headline {
    position: absolute; left: 40px; top: 22px;
    font-family: "Archivo Black", "Arial Black", sans-serif;
    font-size: 74px; line-height: 0.95;
    color: var(--maroon);
    text-transform: uppercase;
    letter-spacing: 1px;
  }
  .info-band {
    position: absolute; left: 0; top: 262px;
    width: 760px; height: 62px;
    background: var(--navy);
    padding: 8px 40px;
    font-family: "Poppins", sans-serif;
    font-weight: 500;
    font-size: 16.5px; line-height: 1.35;
    color: var(--white);
  }
  .contact-band {
    position: absolute; left: 0; top: 324px;
    width: 760px; height: 116px;
    background: var(--ink);
    padding: 20px 40px;
    display: flex; align-items: center; gap: 18px;
    font-family: "Poppins", sans-serif;
  }
  .contact-label { color: var(--white); font-size: 23px; font-weight: 400; }
  .contact-icon { width: 26px; height: 30px; }
  .contact-number { color: var(--number); font-size: 42px; font-weight: 600; letter-spacing: 1px; }
  .visuals { position: absolute; left: 0; top: 0; width: 1160px; height: 440px; }
</style>
</head>
<body>
  <main class="billboard">
    <h1 class="headline">Cielo de<br>Nuestra<br>Espera 4D</h1>

    <p class="info-band">
      Hacemos Ultrasonido en 3D/4d/5D ,10k Y Imagenes<br>
      Hyper-realistic Serviendo la area Oeste de Puerto Rico.
    </p>

    <div class="contact-band">
      <span class="contact-label">Para orientacion</span>
      <svg class="contact-icon" viewBox="0 0 24 28" aria-hidden="true">
        <path d="M7 2 L11 7 L8 10 C9 14 11 17 14 19 L17 16 L21 20 L17 25 C9 23 3 14 3 5 Z" fill="var(--phone-red)"/>
      </svg>
      <span class="contact-number">555-014-2879</span>
    </div>

    <svg class="visuals" viewBox="0 0 1160 440" aria-hidden="false">
      <defs>
        <radialGradient id="scan-tone" cx="0.45" cy="0.45" r="0.7">
          <stop offset="0" stop-color="#c8782c"/>
          <stop offset="0.6" stop-color="#8a4a18"/>
          <stop offset="1" stop-color="#3a1a08"/>
        </radialGradient>
        <radialGradient id="newborn-tone" cx="0.5" cy="0.5" r="0.7">
          <stop offset="0" stop-color="#f2c4b0"/>
          <stop offset="0.7" stop-color="#dc9f8c"/>
          <stop offset="1" stop-color="#6a3a30"/>
        </radialGradient>
      </defs>
      <path class="curve-frame" d="M690 0 Q600 220 700 440 L1160 440 L1160 0 Z" fill="var(--maroon)"/>
      <path class="curve-line" d="M712 0 Q624 220 722 440 L1160 440 L1160 0 Z" fill="var(--white)"/>
      <path d="M718 0 Q630 220 728 440 L905 440 L905 0 Z" fill="url(#scan-tone)"
            role="img" aria-label="Imagen de ultrasonido 4D de un bebé en el vientre"/>
      <rect x="905" y="0" width="14" height="440" fill="#2a1412"/>
      <rect x="919" y="0" width="241" height="440" fill="url(#newborn-tone)"
            role="img" aria-label="Fotografía de un recién nacido dormido"/>
    </svg>
  </main>
</body>
</html>
```